KRL Stationery Design Project

Dear Designers,
We need a new stationery design for company to match our new logo.
Designers should provide a design for the following:
1. Business Card: 3.5x2 Inches.
2. Letterhead: A4 size.
3. Envelops: 25x35.5 Cm.
You can keep the Arabic name at the bottom of the logo Or you can use the separate attached Arabic Name.
Please refer to the attached logo guide for design information.
Sample Business Card information:
Name: Tarek Sowan
Position: Operation Manager
Tel: +966 920007164 Ex. 500
Fax: +966 (3)8842617
Mob: +966 (5)00263817
email: tarek@krl-example.com.sa
URL: www.krl-example.com.sa
Address:
Nakheel Heights, Suite 718
Zayed bin Omar Str.
Khobar, 31847
Saudi Arabia
Updates
Dear All,
Please note, we had uploaded our logo along with Arabic writing in Adobe illustrator format (.ai).
Regards,
Karim
Dear All,
A sample data for the business card had been added as per your request.
Regards,
Karim

```html
<!DOCTYPE html>
<html lang="en">
<head>
<meta charset="utf-8">
<title>KRL Business Card</title>
<link rel="stylesheet" href="https://fonts.googleapis.com/css2?family=Titillium+Web:wght@400;700&display=swap">
<style>
  :root {
    --backdrop: #2b2b2b;
    --card: #ffffff;
    --navy: #002a54;
    --panel-text: #c9d2dd;
    --panel-strong: #ffffff;
    --muted: #4a4f57;
  }
  * { margin: 0; padding: 0; box-sizing: border-box; }
  html, body { width: 1200px; height: 472px; overflow: hidden; }
  body {
    background: var(--backdrop);
    font-family: "Titillium Web", sans-serif;
    position: relative;
  }
  .card {
    position: absolute;
    top: 84px;
    width: 525px;
    height: 299px;
    background: var(--card);
    border-radius: 12px;
    overflow: hidden;
  }
  .card-front { left: 60px; }
  .card-back { left: 603px; }

  .brand {
    position: absolute;
    display: flex;
    align-items: center;
    gap: 10px;
    color: var(--navy);
    font-weight: 700;
    line-height: 1;
  }
  .brand-mark {
    background: var(--navy);
    flex: none;
  }
  .card-front .brand { left: 92px; top: 124px; font-size: 46px; }
  .card-front .brand-mark { width: 22px; height: 22px; }
  .card-back .brand { left: 192px; top: 84px; font-size: 60px; }
  .card-back .brand-mark { width: 28px; height: 28px; }

  .contact-panel {
    position: absolute;
    left: 308px;
    top: 0;
    width: 217px;
    height: 299px;
    background: var(--navy);
    color: var(--panel-text);
    padding: 76px 0 0 16px;
    font-size: 14px;
    line-height: 17px;
  }
  .person { color: var(--panel-strong); font-size: 17px; font-weight: 700; margin-bottom: 20px; }
  .person .title { font-weight: 400; font-size: 14px; color: var(--panel-text); }
  .contact-list { list-style: none; margin-bottom: 14px; }
  .contact-list li { display: flex; align-items: center; gap: 6px; }
  .contact-list svg { width: 11px; height: 11px; fill: var(--panel-text); flex: none; }
  .address { font-style: normal; }

  .back-url {
    position: absolute;
    left: 0; right: 0;
    top: 244px;
    text-align: center;
    font-size: 13px;
    letter-spacing: 3px;
    color: var(--muted);
  }
</style>
</head>
<body>
  <section class="card card-front">
    <div class="brand"><span class="brand-mark"></span>KRL</div>
    <div class="contact-panel">
      <p class="person">Your Name, <span class="title">Title</span></p>
      <ul class="contact-list">
        <li><svg viewBox="0 0 12 12" aria-hidden="true"><path d="M2.5 0.8l2 2.2-1 1.3c.7 1.6 2 2.9 3.6 3.6l1.3-1 2.2 2-1.2 2.1C5 10.5 1.5 7 0.4 2z"/></svg>123-456-7890</li>
        <li><svg viewBox="0 0 12 12" aria-hidden="true"><path d="M2 5l1.2-3h5.6L10 5h1v4H9.5v1.5h-1.5V9H4v1.5H2.5V9H1V5zm1.4 0h5.2l-.7-2H4.1z"/></svg>123-456-7890</li>
        <li><svg viewBox="0 0 12 12" aria-hidden="true"><path d="M1 3h10v6.5H1zm1 .8L6 6.6 10 3.8z"/></svg>info@mailbox-example.com</li>
        <li><svg viewBox="0 0 12 12" aria-hidden="true"><circle cx="6" cy="6" r="5.2"/></svg>www.website.com</li>
      </ul>
      <address class="address">Street Name, City Name<br>State, City Zip Code</address>
    </div>
  </section>

  <section class="card card-back">
    <div class="brand"><span class="brand-mark"></span>KRL</div>
    <p class="back-url">www.website.com</p>
  </section>
</body>
</html>
```